Sophisticated, clean website reflecting my feminine, playful side to sell my abstract art,

I need a website no more than 3 pages to showcase my paintings, a little about me and some contact info. I do abstracts so looking for something a little edgy, yet feminine and current.
Updates

Hi there, These are some artists websites that I Iike: Marnelvoss.com (I like how airy it is) peterwallombry.com garethpolvens.com (I like how it scrolls) I'll need a place for a photo ( a headshot-i do not have it yet so I'll need to be able to upload that later) as well as an area for my bio. Also, it's important that I will be able to upload any new photos and descriptions easily so it should be user friendly. Lastly, I like in a sunny place so would like to have this seem upbeat and playful as that is how i like to paint. thanks-I'm trying to upload my photos now -

Target Market(s)

ppl ages 35-70 who want large scale art for their homes

Industry/Entity Type

art

Coding

Coded - Design and coding required

Number of Pages Required

3 page

Colors

Designer to choose colors to be used in the design.

Requirements
Must have
• photos of my art, a place for my bio, be easy to reach me. tasteful-nothing too "in your face" -my clients are pretty high end and organized. They like clean lines
Nice to have
• sophisticated background, muted tones in the back-similar clean font throughout-no cursive
Should not have
• too many dark areas. Too many blocks of color. Too serious.

```html
<!DOCTYPE html>
<html lang="en">
<head>
<meta charset="utf-8">
<title>Marlowe Brandt — Abstract Art</title>
<link href="https://fonts.googleapis.com/css2?family=Bebas+Neue&family=Barlow:wght@400;500;600&family=Nunito+Sans:wght@400&display=swap" rel="stylesheet">
<style>
  :root {
    --ink: #0b0b0b;
    --white: #ffffff;
    --nav-band: #e8e8e8;
    --divider: #b9b9b9;
    --tan: #b98e5c;
    --tan-text: #c08a50;
    --sage: #bdb58f;
    --text: #2a2a2a;
    --field-line: #c9c9c9;
    --peach: #f5c99a;
  }
  * { box-sizing: border-box; margin: 0; padding: 0; }
  html, body { width: 1200px; height: 3052px; overflow: hidden; background: var(--white); }
  body { position: relative; font-family: "Nunito Sans", sans-serif; color: var(--text); }
  .abs { position: absolute; }

  /* header */
  .brand { position: absolute; display: flex; align-items: center; gap: 14px; }
  .brand-square { width: 58px; height: 58px; border: 4px solid var(--ink); background: var(--white); }
  .brand-name { font-family: "Bebas Neue", sans-serif; font-size: 52px; color: var(--ink); line-height: 1; padding-top: 4px; white-space: nowrap; }
  .header-brand { left: 400px; top: 30px; }
  .follow { left: 929px; top: 42px; display: flex; align-items: center; gap: 14px; }
  .follow-label { font-family: "Bebas Neue", sans-serif; font-size: 22px; color: var(--ink); }
  .social-dot { width: 34px; height: 34px; border-radius: 50%; border: 4px solid var(--ink); }

  .nav-band { left: 0; top: 114px; width: 1200px; height: 61px; background: var(--nav-band); }
  .nav-item { position: absolute; top: 131px; font-family: "Bebas Neue", sans-serif; font-size: 25px; color: var(--ink); transform: translateX(-50%); white-space: nowrap; }
  .nav-item.is-active::after { content: ""; position: absolute; left: 0; right: 0; bottom: -4px; height: 2px; background: var(--ink); }
  .nav-sep { position: absolute; top: 132px; width: 2px; height: 24px; background: var(--divider); }

  /* hero */
  .hero { left: 0; top: 175px; width: 1200px; height: 652px;
    background:
      radial-gradient(circle at 30% 40%, #3f9b45 0%, transparent 35%),
      radial-gradient(circle at 75% 70%, #0f6e73 0%, transparent 35%),
      radial-gradient(circle at 90% 25%, #6b4a2a 0%, transparent 30%),
      radial-gradient(circle at 55% 15%, #2f8d6a 0%, transparent 30%),
      radial-gradient(circle at 10% 80%, #d9d6e4 0%, transparent 35%),
      linear-gradient(120deg, #cfd8cf, #6aa86a 45%, #2f7f78 70%, #4a3a2a); }
  .hero-title { position: absolute; left: 122px; color: var(--white); font-family: "Bebas Neue", sans-serif; line-height: 1; white-space: nowrap; }
  .hero-title.small { top: 402px; font-size: 66px; }
  .hero-title.big { top: 466px; font-size: 90px; }
  .hero-arrow { position: absolute; top: 443px; }

  /* about */
  .about-frame { left: 127px; top: 969px; width: 323px; height: 379px; border-left: 4px solid var(--tan); border-bottom: 4px solid var(--tan); border-bottom-left-radius: 60px; }
  .about-photo { left: 140px; top: 945px; width: 362px; height: 394px; border-top-right-radius: 70px;
    background: radial-gradient(ellipse at 50% 70%, #a9b0b6 0%, #c9b6a2 40%, var(--peach) 70%); }
  .section-title { font-family: "Bebas Neue", sans-serif; font-size: 54px; color: var(--ink); line-height: 1; font-weight: 400; }
  .title-rule { height: 3px; background: var(--sage); }
  .about-title { left: 575px; top: 964px; }
  .about-rule { left: 575px; top: 1020px; width: 73px; }
  .about-copy { left: 578px; top: 1046px; width: 496px; height: 210px; font-size: 15.6px; line-height: 27px; text-align: justify; overflow: hidden; }
  .about-copy p + p { margin-top: 15px; }
  .btn-outline { position: absolute; border: 2px solid var(--ink); font-family: "Barlow", sans-serif; font-weight: 600; color: var(--tan-text); display: flex; align-items: center; justify-content: center; }
  .about-btn { left: 575px; top: 1279px; width: 178px; height: 48px; font-size: 17px; }

  /* gallery */
  .brush { left: 0; top: 1430px; width: 1200px; height: 800px; }
  .gallery-title { left: 0; width: 1200px; top: 1522px; text-align: center; }
  .gallery-rule { left: 571px; top: 1586px; width: 69px; }
  .tile { position: absolute; }
  .gallery-btn { left: 484px; top: 2090px; width: 214px; height: 57px; font-size: 21px; }

  /* contact */
  .contact-title { left: 95px; top: 2342px; }
  .contact-rule { left: 95px; top: 2407px; width: 76px; }
  .contact-intro { left: 95px; top: 2425px; width: 430px; font-size: 17px; line-height: 29px; }
  .icon-circle { position: absolute; width: 70px; height: 70px; border-radius: 50%; background: var(--sage); display: flex; align-items: center; justify-content: center; }
  .contact-label { position: absolute; font-family: "Barlow", sans-serif; font-size: 17px; color: var(--ink); text-transform: uppercase; white-space: nowrap; }
  .contact-value { position: absolute; font-family: "Barlow", sans-serif; font-size: 22px; color: var(--ink); white-space: nowrap; }
  .form-card { left: 554px; top: 2312px; width: 545px; height: 410px; background: var(--white); border-radius: 70px 70px 0 70px; box-shadow: 0 6px 40px rgba(0,0,0,0.08); }
  .field { position: absolute; left: 612px; width: 421px; border-bottom: 2px solid var(--field-line); font-family: "Barlow", sans-serif; font-size: 17px; color: var(--ink); padding-left: 2px; }
  .submit { left: 612px; top: 2620px; width: 157px; height: 42px; background: var(--ink); color: var(--white); font-family: "Barlow", sans-serif; font-weight: 600; font-size: 16px; display: flex; align-items: center; justify-content: center; }

  /* footer */
  .footer { left: 0; top: 2838px; width: 1200px; height: 214px; background: var(--ink); }
  .footer-brand { left: 89px; top: 2884px; gap: 12px; }
  .footer-brand .brand-square { width: 42px; height: 42px; border-color: var(--white); background: var(--ink); }
  .footer-brand .brand-name { color: var(--white); font-size: 38px; }
  .footer-link { position: absolute; top: 2892px; font-family: "Bebas Neue", sans-serif; font-size: 25px; color: var(--white); white-space: nowrap; }
  .footer-social { left: 990px; top: 2886px; width: 34px; height: 34px; border-radius: 50%; border: 4px solid var(--white); }
  .footer-rule { left: 73px; top: 2966px; width: 993px; height: 1px; background: #555; }
  .copyright { left: 0; width: 1200px; top: 2990px; text-align: center; font-family: "Barlow", sans-serif; font-size: 12px; color: #cfcfcf; }
</style>
</head>
<body>

<header>
  <div class="brand header-brand">
    <span class="brand-square"></span>
    <span class="brand-name">Marlowe Brandt</span>
  </div>
  <div class="abs follow">
    <span class="follow-label">Follow on:</span>
    <span class="social-dot"></span>
  </div>
  <div class="abs nav-band"></div>
  <nav>
    <span class="nav-item is-active" style="left:229px">Home</span>
    <span class="nav-sep" style="left:314px"></span>
    <span class="nav-item" style="left:425px">About Me</span>
    <span class="nav-sep" style="left:532px"></span>
    <span class="nav-item" style="left:636px">Gallery</span>
    <span class="nav-sep" style="left:736px"></span>
    <span class="nav-item" style="left:845px">Contact</span>
    <span class="nav-sep" style="left:939px"></span>
  </nav>
</header>

<section>
  <div class="abs hero" role="img" aria-label="Abstract painting with green, teal and brown brushstrokes"></div>
  <div class="hero-title small">Welcome to</div>
  <div class="hero-title big">Marlowe Brandt</div>
  <svg class="hero-arrow" style="left:34px" width="30" height="48" viewBox="0 0 30 48"><polyline points="24,4 6,24 24,44" fill="none" stroke="#fff" stroke-width="6" stroke-linecap="round" stroke-linejoin="round"/></svg>
  <svg class="hero-arrow" style="left:1136px" width="30" height="48" viewBox="0 0 30 48"><polyline points="6,4 24,24 6,44" fill="none" stroke="#fff" stroke-width="6" stroke-linecap="round" stroke-linejoin="round"/></svg>
</section>

<section>
  <div class="abs about-frame"></div>
  <div class="abs about-photo" role="img" aria-label="Portrait photo of the artist"></div>
  <h2 class="abs section-title about-title">About Me</h2>
  <div class="abs title-rule about-rule"></div>
  <div class="abs about-copy">
    <p>Lorem ipsum dolor sit amet, consectetur adipiscing elit, sed do eiusmod tempor incididunt ut labore et dolore magna aliqua. Ut enim ad minim veniam, quis nostrud exercitation ullamco laboris</p>
    <p>Duis aute irure dolor in reprehenderit in voluptate velit esse cillum dolore eu fugiat nulla pariatur. Excepteur sint occaecat cupidatat non proident, sunt in culpa qui officia deserunt mollit anim id est laborum.Sed ut perspiciatis unde omnis iste natus err</p>
  </div>
  <span class="btn-outline about-btn">LEARN MORE</span>
</section>

<section>
  <svg class="abs brush" viewBox="0 0 1200 800" role="img" aria-label="Soft beige brushstroke behind the gallery">
    <defs>
      <linearGradient id="strokeFade" x1="0" y1="1" x2="1" y2="0">
        <stop offset="0" stop-color="#f1e2d6" stop-opacity="0.5"/>
        <stop offset="0.5" stop-color="#ecd8c8"/>
        <stop offset="1" stop-color="#e6c9b4"/>
      </linearGradient>
    </defs>
    <path d="M0 340 C200 260 500 170 1200 0 L1200 380 C900 520 500 650 170 800 L120 720 C80 620 40 520 0 480 Z" fill="url(#strokeFade)"/>
  </svg>
  <h2 class="abs section-title gallery-title">Our Gallery</h2>
  <div class="abs title-rule gallery-rule"></div>

  <div class="tile" style="left:89px;top:1641px;width:241px;height:192px;background:linear-gradient(135deg,#6a4f86,#b3a3c6 50%,#e7e1e6)" role="img" aria-label="Purple floral abstract painting"></div>
  <div class="tile" style="left:89px;top:1846px;width:241px;height:190px;background:linear-gradient(135deg,#e9e6dc,#6a9ac6 45%,#d6a640 75%,#f0ece4)" role="img" aria-label="Blue and yellow abstract painting"></div>
  <div class="tile" style="left:344px;top:1641px;width:241px;height:395px;background:linear-gradient(160deg,#dcdde3,#5fa84a 40%,#2e7f52 70%,#9bc86a)" role="img" aria-label="Green abstract painting"></div>
  <div class="tile" style="left:598px;top:1641px;width:241px;height:192px;background:linear-gradient(90deg,#e8e1cf 0 25%,#0f8a7e 25% 75%,#e8e1cf 75%)" role="img" aria-label="Teal band abstract painting"></div>
  <div class="tile" style="left:598px;top:1846px;width:241px;height:190px;background:linear-gradient(135deg,#5b3b34,#c9a3a3 50%,#efe7e2)" role="img" aria-label="Rose toned floral painting"></div>
  <div class="tile" style="left:853px;top:1641px;width:242px;height:395px;background:linear-gradient(160deg,#cfd2d2,#2f93a8 30%,#c0703a 55%,#1f2a2a 80%,#3a8a7a)" role="img" aria-label="Teal, orange and black abstract painting"></div>

  <span class="btn-outline gallery-btn">VIEW MORE</span>
</section>

<section>
  <h2 class="abs section-title contact-title">Contact</h2>
  <div class="abs title-rule contact-rule"></div>
  <p class="abs contact-intro">Lorem ipsum dolor sit amet, consectetur adipiscing elit, sed do eiusmod tempor incididunt ut</p>

  <div class="icon-circle" style="left:95px;top:2516px">
    <svg width="34" height="34" viewBox="0 0 24 24"><path d="M6.6 10.8a15.1 15.1 0 0 0 6.6 6.6l2.2-2.2a1 1 0 0 1 1-.25 11.4 11.4 0 0 0 3.6.57 1 1 0 0 1 1 1V20a1 1 0 0 1-1 1A17 17 0 0 1 3 4a1 1 0 0 1 1-1h3.5a1 1 0 0 1 1 1c0 1.25.2 2.45.57 3.57a1 1 0 0 1-.25 1z" fill="#fff"/></svg>
  </div>
  <span class="contact-label" style="left:184px;top:2530px">Phone Number</span>
  <span class="contact-value" style="left:183px;top:2550px">(123) 456 7890</span>

  <div class="icon-circle" style="left:95px;top:2614px">
    <svg width="38" height="28" viewBox="0 0 38 28"><rect x="2" y="2" width="34" height="24" fill="none" stroke="#fff" stroke-width="2.5"/><polyline points="2,2 19,16 36,2" fill="none" stroke="#fff" stroke-width="2.5"/><line x1="2" y1="26" x2="15" y2="13" stroke="#fff" stroke-width="2.5"/><line x1="36" y1="26" x2="23" y2="13" stroke="#fff" stroke-width="2.5"/></svg>
  </div>
  <span class="contact-label" style="left:187px;top:2622px;font-size:15px">Email Us</span>
  <span class="contact-value" style="left:187px;top:2644px;font-size:21px">hello@marlowebrandt.com</span>

  <div class="abs form-card"></div>
  <span class="field" style="top:2362px;height:26px">NAME</span>
  <span class="field" style="top:2420px;height:30px">EMAIL ADDRESS</span>
  <span class="field" style="top:2477px;height:27px">PHONE</span>
  <span class="field" style="top:2534px;height:67px">MESSAGE</span>
  <span class="abs submit">SUBMIT</span>
</section>

<footer>
  <div class="abs footer"></div>
  <div class="brand footer-brand">
    <span class="brand-square"></span>
    <span class="brand-name">Marlowe Brandt</span>
  </div>
  <span class="footer-link" style="left:434px">Home</span>
  <span class="footer-link" style="left:538px">About Me</span>
  <span class="footer-link" style="left:678px">Gallery</span>
  <span class="footer-link" style="left:812px">Contact</span>
  <span class="abs footer-social"></span>
  <div class="abs footer-rule"></div>
  <p class="abs copyright">© 2022 MARLOWE BRANDT | ALL RIGHTS RESERVED</p>
</footer>

</body>
</html>
```